Business Card Design Project

Business card based on attached logo

Todd Merrick
Todd@lorvantest.com
877-514-9073 ext. 318
Www.LorvanTest.com

Industry/Entity Type

Business

```html
<!DOCTYPE html>
<html lang="en">
<head>
<meta charset="utf-8">
<title>LorvanTest Business Cards</title>
<link rel="stylesheet" href="https://fonts.googleapis.com/css2?family=Arimo:wght@400;700&display=swap">
<style>
  :root {
    --brand-red: #ed1c24;
    --brand-black: #231f20;
    --paper-white: #ffffff;
    --backdrop: #e8e5e1;
    --card-edge: rgba(0, 0, 0, 0.35);
  }
  html, body {
    margin: 0;
    padding: 0;
    width: 1200px;
    height: 746px;
    overflow: hidden;
    background: var(--backdrop);
  }
  .sheet {
    position: relative;
    width: 1200px;
    height: 746px;
  }
  .card {
    position: absolute;
    width: 538px;
    height: 307px;
    box-sizing: border-box;
    border: 1px solid var(--card-edge);
    font-family: "Arimo", Arial, sans-serif;
  }
  .card--red   { left: 49px;  top: 49px;  background: var(--brand-red);   color: var(--paper-white); }
  .card--black { left: 620px; top: 49px;  background: var(--brand-black); color: var(--paper-white); }
  .card--white { left: 258px; top: 396px; background: var(--paper-white); color: var(--brand-black); }

  .wordmark {
    position: absolute;
    left: 0;
    right: 0;
    top: 92px;
    display: flex;
    justify-content: center;
    align-items: center;
    gap: 14px;
  }
  .wordmark__name {
    font-weight: 700;
    font-size: 60px;
    line-height: 1;
    letter-spacing: -1px;
  }
  .wordmark__square {
    width: 40px;
    height: 40px;
    margin-top: -46px;
    background: currentColor;
  }
  .card--white .wordmark { color: var(--brand-red); }

  .tagline {
    position: absolute;
    left: 0;
    right: 0;
    top: 238px;
    margin: 0;
    text-align: center;
    font-weight: 400;
    font-size: 17px;
    letter-spacing: 3.2px;
  }
  .web {
    position: absolute;
    left: 0;
    right: 12px;
    top: 273px;
    margin: 0;
    text-align: center;
    font-weight: 400;
    font-size: 17px;
    letter-spacing: 3.2px;
  }
</style>
</head>
<body>
  <main class="sheet">
    <section class="card card--red">
      <div class="wordmark"><span class="wordmark__name">LorvanTest</span><span class="wordmark__square"></span></div>
      <p class="tagline">Expert Online HIPAA Training</p>
      <p class="web">www.LorvanTest.com</p>
    </section>

    <section class="card card--black">
      <div class="wordmark"><span class="wordmark__name">LorvanTest</span><span class="wordmark__square"></span></div>
      <p class="tagline">Expert Online HIPAA Training</p>
      <p class="web">www.LorvanTest.com</p>
    </section>

    <section class="card card--white">
      <div class="wordmark"><span class="wordmark__name">LorvanTest</span><span class="wordmark__square"></span></div>
      <p class="tagline">Expert Online HIPAA Training</p>
      <p class="web">www.LorvanTest.com</p>
    </section>
  </main>
</body>
</html>
```